Computer consultant business card

Bexil Software is a newly started computer consulting company. It's a small one-man company that provides mostly Vornix applications but also websites in collaboration with designers. I'm running this company on the side of full time university studies.

I want the final design to be clean and memorable. Be creative! :)

Some inspiration:
http://www.pixelmarta.com/design/48317
http://www.pixelmarta.com/design/2739164/business-card-design-by-frostlynk
http://www.pixelmarta.com/design/604281/business-card-design-by-koralind-vestrabanu

See attachment for my company logo.
Updates

I would like to thank everyone for submitting! I'll need a couple of days to review and ultimately select a design.

Target Market(s)

Non-technical entrepreneurs and small companies.

Industry/Entity Type

University

Requirements
Must have
• My company logo.
In any way, both colors from my logo.
First- and last name, e-mail and phone number.
Double-sided design.
Nice to have
• Something creative with the symbol in my logo

```html
<!DOCTYPE html>
<html lang="en">
<head>
<meta charset="utf-8">
<title>Bexil Software – Business Card</title>
<link rel="stylesheet" href="https://fonts.googleapis.com/css2?family=Open+Sans:wght@400;600&family=PT+Serif&display=swap">
<style>
  :root {
    --slate: #2f3741;
    --slate-light: #3d4651;
    --paper: #f3f4f5;
    --paper-shade: #e2e4e7;
    --brand-blue: #7aa6dc;
    --brand-gray: #4b5057;
    --text-light: #dfe4ea;
    --backdrop: #ece9e4;
  }
  * { margin: 0; padding: 0; box-sizing: border-box; }
  html, body { width: 690px; height: 1200px; overflow: hidden; }
  body {
    background: var(--backdrop);
    font-family: "Open Sans", Arial, sans-serif;
    position: relative;
  }
  .card {
    position: absolute;
    left: 65px;
    width: 560px;
    height: 320px;
    border-radius: 4px;
    overflow: hidden;
    box-shadow: 0 10px 24px rgba(0,0,0,0.22);
  }
  .card--front { top: 190px; background: linear-gradient(180deg, var(--slate-light), var(--slate)); }
  .card--back  { top: 690px; background: var(--paper); }

  .front-band {
    position: absolute;
    left: 0; right: 0; top: 100px; height: 120px;
    background: linear-gradient(180deg, var(--paper), var(--paper-shade));
    display: flex; align-items: center; justify-content: center;
  }
  .wordmark {
    display: flex; align-items: center; gap: 14px;
  }
  .wordmark__dot {
    width: 34px; height: 34px; border-radius: 50%;
    background: var(--brand-blue);
  }
  .wordmark__name {
    font-family: "Open Sans", Arial, sans-serif;
    font-weight: 600;
    font-size: 54px;
    letter-spacing: -1px;
    color: var(--brand-gray);
    line-height: 1;
  }

  .back-top {
    position: absolute; left: 0; right: 0; top: 0; height: 150px;
    background: linear-gradient(180deg, var(--paper), var(--paper-shade));
    display: flex; align-items: center; justify-content: center;
  }
  .back-divider {
    position: absolute; left: 0; right: 0; top: 150px; height: 4px;
    background: var(--brand-blue);
  }
  .back-stitch {
    position: absolute; left: 0; right: 0; top: 160px;
    border-top: 1px dashed rgba(122,166,220,0.6);
  }
  .back-bottom {
    position: absolute; left: 0; right: 0; top: 154px; bottom: 0;
    background: linear-gradient(180deg, var(--slate-light), var(--slate));
  }
  .holder {
    position: absolute; left: 34px; bottom: 40px;
  }
  .holder__name {
    font-family: "PT Serif", Georgia, serif;
    font-size: 24px; color: var(--brand-blue);
  }
  .holder__role {
    font-size: 12px; color: var(--text-light); margin-top: 2px;
  }
  .contacts {
    position: absolute; right: 34px; top: 28px;
    list-style: none;
  }
  .contacts__item {
    display: flex; align-items: center; gap: 10px;
    font-size: 12.5px; color: var(--text-light);
    line-height: 24px;
  }
  .contacts__icon { width: 13px; height: 13px; flex: none; }
</style>
</head>
<body>

<section class="card card--front" aria-label="Card front">
  <div class="front-band">
    <div class="wordmark">
      <span class="wordmark__dot"></span>
      <span class="wordmark__name">bexil</span>
    </div>
  </div>
</section>

<section class="card card--back" aria-label="Card back">
  <div class="back-top">
    <div class="wordmark">
      <span class="wordmark__dot"></span>
      <span class="wordmark__name">bexil</span>
    </div>
  </div>
  <div class="back-bottom">
    <ul class="contacts">
      <li class="contacts__item">
        <svg class="contacts__icon" viewBox="0 0 16 16"><path fill="#7aa6dc" d="M3.5 1l2.5 3-1.5 2c1 2 3 4 5 5l2-1.5 3 2.5-1.5 2.5C7 15 1 9 1 2.5z"/></svg>
        +123 555 014
      </li>
      <li class="contacts__item">
        <svg class="contacts__icon" viewBox="0 0 16 16"><rect x="1" y="3" width="14" height="10" rx="1" fill="#7aa6dc"/><path d="M1.5 3.5L8 9l6.5-5.5" stroke="#2f3741" stroke-width="1.4" fill="none"/></svg>
        info@bexilsoft.com
      </li>
      <li class="contacts__item">
        <svg class="contacts__icon" viewBox="0 0 16 16"><circle cx="8" cy="8" r="6.5" stroke="#7aa6dc" stroke-width="1.6" fill="none"/><path d="M1.5 8h13M8 1.5c-3 3.5-3 9.5 0 13M8 1.5c3 3.5 3 9.5 0 13" stroke="#7aa6dc" stroke-width="1.2" fill="none"/></svg>
        www.bexilsoft.com
      </li>
      <li class="contacts__item">
        <svg class="contacts__icon" viewBox="0 0 16 16"><path fill="#7aa6dc" d="M8 1a5 5 0 0 0-5 5c0 4 5 9 5 9s5-5 5-9a5 5 0 0 0-5-5zm0 7a2 2 0 1 1 0-4 2 2 0 0 1 0 4z"/></svg>
        4821 Corlan St Dunmore, CA 90417
      </li>
    </ul>
    <div class="holder">
      <p class="holder__name">Marten Holby</p>
      <p class="holder__role">General Manager</p>
    </div>
  </div>
  <div class="back-divider"></div>
  <div class="back-stitch"></div>
</section>

</body>
</html>
```